The most modern business card ever !!!

Our company call “Vendalo”. Vendalo is a technology company specialized in cruises solutions. Out main product is a platform to reserve cruises. This is a revolutionary platform that make easier to travel agencies and final users to reserve cruises across dozen companies like tibba, wernu, hpv, dgb, etc..We are a “start up”, with a young team of developers and we want to transmit it.. For it, we want something different, a modern business card that represent cruises and technology.. When someone receive this card, this person should say: wowww this is different… this is modern… this is a cruise related company..
- diferent, modern
- traditions business card

```html
<!DOCTYPE html>
<html lang="en">
<head>
<meta charset="utf-8">
<title>Vendalo Business Card</title>
<link rel="stylesheet" href="https://fonts.googleapis.com/css2?family=Exo+2:wght@500&family=Roboto:wght@300;400;500&display=swap">
<style>
  :root {
    --backdrop: #e8e5df;
    --navy: #101844;
    --navy-glow: #2a2a6a;
    --sky: #29a8e0;
    --white: #ffffff;
    --ink: #111111;
    --soft-white: #d9dcea;
    --card-shadow: rgba(0, 0, 0, 0.25);
  }
  * { margin: 0; padding: 0; box-sizing: border-box; }
  html, body {
    width: 1200px;
    height: 1200px;
    overflow: hidden;
    background: var(--backdrop);
  }
  .canvas {
    position: relative;
    width: 1200px;
    height: 1200px;
  }
  .card {
    position: absolute;
    top: 252px;
    width: 417px;
    height: 696px;
    box-shadow: 0 6px 18px var(--card-shadow);
    font-family: "Roboto", sans-serif;
  }

  /* Front */
  .card-front {
    left: 160px;
    background: radial-gradient(circle at 50% 27%, var(--navy-glow) 0%, var(--navy) 45%, var(--navy) 100%);
  }
  .front-brand {
    position: absolute;
    left: 72px;
    top: 160px;
    font-family: "Exo 2", sans-serif;
    font-weight: 500;
    font-size: 58px;
    letter-spacing: 1px;
    color: var(--white);
  }
  .front-marker {
    position: absolute;
    left: 72px;
    top: 522px;
    width: 9px;
    height: 52px;
    background: var(--white);
  }
  .front-marker.accent { left: 86px; background: var(--sky); }
  .front-identity {
    position: absolute;
    left: 135px;
    top: 522px;
  }
  .front-identity .name {
    font-size: 20px;
    font-weight: 500;
    letter-spacing: 2px;
    color: var(--white);
    line-height: 28px;
  }
  .front-identity .role {
    font-size: 17px;
    font-weight: 300;
    letter-spacing: 2px;
    color: var(--soft-white);
    line-height: 24px;
  }

  /* Back */
  .card-back {
    left: 624px;
    background: var(--white);
  }
  .back-identity {
    position: absolute;
    left: 64px;
    bottom: 382px;
    writing-mode: vertical-rl;
    transform: rotate(180deg);
    text-align: start;
  }
  .back-identity .name {
    font-size: 18px;
    font-weight: 500;
    letter-spacing: 3px;
    color: var(--ink);
    line-height: 24px;
  }
  .back-identity .role {
    font-size: 16px;
    font-weight: 300;
    letter-spacing: 2px;
    color: var(--ink);
    line-height: 24px;
  }
  .back-stripe {
    position: absolute;
    left: 62px;
    width: 53px;
    height: 8px;
  }
  .back-stripe.dark { top: 354px; background: var(--ink); }
  .back-stripe.accent { top: 369px; background: var(--sky); }
  .back-rule {
    position: absolute;
    left: 276px;
    top: 108px;
    width: 10px;
    height: 270px;
    background: var(--sky);
  }
  .back-brand {
    position: absolute;
    left: 308px;
    top: 104px;
    writing-mode: vertical-rl;
    font-family: "Exo 2", sans-serif;
    font-weight: 500;
    font-size: 60px;
    letter-spacing: 1px;
    line-height: 60px;
    color: var(--ink);
  }
  .back-divider {
    position: absolute;
    left: 62px;
    top: 500px;
    width: 118px;
    height: 8px;
    background: var(--sky);
  }
  .contact-list {
    position: absolute;
    left: 62px;
    top: 538px;
    list-style: none;
  }
  .contact-list li {
    font-size: 18px;
    letter-spacing: 1.2px;
    color: var(--ink);
    line-height: 36px;
  }
</style>
</head>
<body>
<main class="canvas">
  <section class="card card-front" aria-label="Card front">
    <div class="front-brand">Vendalo</div>
    <span class="front-marker"></span>
    <span class="front-marker accent"></span>
    <div class="front-identity">
      <p class="name">Your Name Here</p>
      <p class="role">Designation</p>
    </div>
  </section>

  <section class="card card-back" aria-label="Card back">
    <div class="back-identity">
      <p class="name">Your Name Here</p>
      <p class="role">Designation</p>
    </div>
    <span class="back-stripe dark"></span>
    <span class="back-stripe accent"></span>
    <span class="back-rule"></span>
    <div class="back-brand">Vendalo</div>
    <span class="back-divider"></span>
    <ul class="contact-list">
      <li>- Contact@me.com</li>
      <li>- 123 +4567 8910 111</li>
      <li>- Main Avenue Street 123. Etc</li>
    </ul>
  </section>
</main>
</body>
</html>
```